Logo and Website Design for QR.KA Horizon - a Software Engineering and IT company

Software engineering and IT are two different disciplines - and yet inseparably linked. At QR.KA Horizon, we combine both worlds and ensure that our software solutions are not only innovative and powerful, but also integrate perfectly into existing IT landscapes. Vision stands more for imagination, so it is not neccessary something what has to do with visualisation. Please consider that the winning competitor is also instructed to make a logo for the company. So please make a suitable logo for QR.KA Horizon to which the website fits to and show it during the website creation process. A good Logo desing is important for winning the competition. The website should contain a landing page with inspiring, perhaps futuristic photos of a datacenter and lines of code. Eventuelly flewent integrated in the text. On the landing page the company should introduced with a small text (max 250 words) followed by a section with a short text to one of our products nearby a graphic visualising the architecture of the product. The menue should be on top and fixed during scrolling and consist of the menue items home, solutions, who are we and a contact button. There should be a footer for linking social media, rights and Impressum. Only as an idea not a must. The very first view on the landing page could also be the menue bar and below of it a transparent unsharp photo (e.g. datacenter, lines of code, both ;) with the company name in the center.

###############################################################

Hi Designers,

Despite your very good approaches for describing QR.KA Horizon, here a short introduction (german text) from ourself:

------
QR.KA Horizon – Ihr Partner für ganzheitliche Softwarelösungen

Die QR.KA Horizon ist ein dynamisches Unternehmen, das sich nicht nur auf die Konzeption, das Design und die Entwicklung maßgeschneiderter Software spezialisiert hat, sondern auch deren reibungslosen Betrieb sicherstellt. Mit einem Team aus erfahrenen Softwarearchitekten und IT-Professionals verbinden wir modernste Softwareentwicklung mit tiefgehendem IT-Know-how – für Lösungen, die nachhaltig, leistungsstark und zukunftssicher sind.

Software Engineering trifft IT – Perfektion in Kombination
Software Engineering und IT sind zwei unterschiedliche Disziplinen – und doch untrennbar miteinander verbunden. Wir bei QR.KA Horizon vereinen beide Welten und sorgen dafür, dass unsere Softwarelösungen nicht nur innovativ und leistungsfähig sind, sondern sich auch perfekt in bestehende IT-Landschaften integrieren.

Expertise mit Fokus auf Healthcare & komplexe IT-Umgebungen
Unsere Experten bringen jahrzehntelange Erfahrung aus dem Healthcare-Sektor mit und unterstützen IT-Abteilungen großer Kliniken in der Entwicklung und Optimierung von Softwarelösungen. Von Anwendungssoftware bis hin zu Steuerungssystemen – unsere Softwareingenieure wissen genau, worauf es ankommt.

Ganzheitlicher Ansatz – über die Software hinaus
Wir entwickeln nicht nur Software, sondern übernehmen auch die Verantwortung für deren stabile und effiziente Betriebsumgebung. Egal, ob on-premises, in der Cloud oder als SaaS-Lösung – wir kümmern uns um den kompletten Lifecycle Ihrer Anwendung.

Ihre Vision – unsere Mission.
Ob Neuentwicklung einer SaaS-Anwendung oder die Migration bestehender Lösungen in eine moderne SaaS-Umgebung – mit QR.KA Horizon haben Sie einen starken Partner an Ihrer Seite.

Lassen Sie uns gemeinsam die Zukunft Ihrer Software gestalten!
--------------

Our first solution called "Clear Record Transfer Gateway" (CLURA)
-------------------
Teilen Sie Ihre Daten sicher – ohne Kompromisse!

Sie nutzen eine relationale Datenbank (Brightcask, Tabulon Hub, Vellumdb etc.) und möchten ausgewählte Daten mit Dritten teilen – sei es für ein Data Warehouse, Business Controller, Lieferanten oder Kunden? Doch dabei sollen Datensicherheit, Integrität und Verfügbarkeit Ihrer primären Lösung in keiner Weise gefährdet werden?

Mit unserer Lösung erhalten Sie genau das: Maximalen Schutz für Ihre Anwendung bei gleichzeitigem Nutzen durch autorisierte Dritte – ganz ohne teure Lizenzkosten für eine Schattendatenbank.

Lassen Sie uns gemeinsam herausfinden, wie Sie Ihre Daten sicher und effizient nutzen können. Kontaktieren Sie uns – wir zeigen Ihnen, was möglich ist!
---------------------

Our second solution MIVO:
---------------------
MIVO – Program for a Tone Matching Instrument ist die smarte Lösung für Unternehmen, die bei Farbgenauigkeit keine Kompromisse machen. Die Software erkennt Farbabweichungen zwischen Mustern vollautomatisch, beschreibt sie verständlich und sorgt so für gleichbleibend hohe Produktqualität – schnell, visuell und präzise. Perfekt für alle, die Farbe zur Vertrauenssache machen.
-------------------------

Thanks,
Gerold

Target Market(s)

IT Professionals from any sector

Industry/Entity Type

Healthcare and other

Coding

Coded - Design and coding required

Number of Pages Required

1 page

Font styles to use
Sans Serif

Colors
0054AA
0677BA
7BADD7
CADEEF
E8F1F8
0094D4
00A9DD
6FCCEA
C7EBF8
E9F6FB
00AB8E
00BBA5
67D7C9
C6EFE9
E9F9F6

Requirements
Must have
• Please see description
Nice to have
• On the landing page the company should introduced with a small text (max 250 words) followed by a section with a short text to one of our products nearby a graphic visualising the architecture of the product. The menue should be on top and fixed during scrolling and consist of the menue items home, solutions, who are we and a contact button. There should be a footer for linking social media, rights and Impressum. Only as an idea not a must. The very first view on the landing page could also be the menue bar and below of it a transparent unsharp photo (e.g. datacenter, lines of code, both ;) with the company name in the center.
Should not have
• Please see description

```html
<!DOCTYPE html>
<html lang="de">
<head>
<meta charset="utf-8">
<title>QR.KA Horizon – Software Engineering &amp; IT</title>
<link href="https://fonts.googleapis.com/css2?family=Montserrat:wght@600;700&family=Poppins:wght@400;500;600&family=Catamaran:wght@400;500;600;700&display=swap" rel="stylesheet">
<style>
:root{
  --blue-900:#0a1a5c;
  --blue-800:#0b2a7a;
  --blue-700:#0054AA;
  --blue-600:#0677BA;
  --blue-500:#0094D4;
  --blue-300:#7BADD7;
  --blue-100:#CADEEF;
  --blue-50:#E8F1F8;
  --green-600:#00AB8E;
  --green-500:#00BBA5;
  --ink:#1d1d1f;
  --white:#ffffff;
}
*{margin:0;padding:0;box-sizing:border-box}
html,body{width:1200px;height:3246px;overflow:hidden}
body{position:relative;background:var(--white);font-family:'Catamaran',sans-serif;color:var(--ink)}

/* Hero */
.hero{position:absolute;left:0;top:0;width:1200px;height:650px;background:linear-gradient(120deg,var(--blue-700) 0%,var(--blue-600) 55%,var(--blue-500) 100%);overflow:hidden}
.hero__band{position:absolute;inset:0;background:linear-gradient(118deg,transparent 42%,rgba(0,148,212,.35) 43%,rgba(0,169,221,.12) 68%,transparent 69%)}
.hero__photo{position:absolute;inset:0;clip-path:polygon(63% 0,100% 0,100% 100%,72% 100%,44% 50%);
  background:
   radial-gradient(ellipse 140px 120px at 82% 37%,rgba(111,204,234,.85) 0%,rgba(0,148,212,.4) 45%,transparent 75%),
   radial-gradient(ellipse 260px 300px at 62% 45%,rgba(6,119,186,.55) 0%,transparent 70%),
   linear-gradient(160deg,#0a2f78 0%,#082157 45%,#041540 100%)}
.nav{position:absolute;left:140px;top:38px;width:918px;height:57px;background:var(--white);border-radius:30px;display:flex;align-items:center;padding:0 10px 0 26px;font-family:'Poppins',sans-serif;z-index:2}
.logo{display:flex;align-items:center;gap:10px;font-family:'Poppins',sans-serif;font-weight:600;font-size:22px;color:var(--blue-700);letter-spacing:.2px}
.logo__dot{width:28px;height:28px;border-radius:50%;border:3px solid currentColor}
.nav__menu{display:flex;gap:40px;margin-left:auto;margin-right:36px;font-size:13px;color:#222}
.nav__menu span{position:relative}
.nav__menu .is-active::before,.nav__menu .is-active::after{content:"";position:absolute;left:50%;transform:translateX(-50%);width:22px;height:3px;background:var(--blue-500)}
.nav__menu .is-active::before{top:-28px}.nav__menu .is-active::after{bottom:-28px}
.caret{font-size:8px;margin-left:4px}
.nav__cta{background:var(--blue-700);color:var(--white);font-size:14px;font-weight:500;padding:10px 28px;border-radius:22px}
.hero__title{position:absolute;left:140px;top:193px;font-family:'Montserrat',sans-serif;font-weight:700;font-size:44px;line-height:59px;color:var(--white)}
.hero__sub{position:absolute;left:140px;top:384px;font-family:'Poppins',sans-serif;font-weight:500;font-size:15px;line-height:27px;color:var(--white)}
.hero__btn{position:absolute;left:140px;top:466px;width:190px;height:38px;border-radius:20px;background:var(--white);color:var(--blue-700);font-family:'Poppins',sans-serif;font-weight:600;font-size:14px;display:flex;align-items:center;justify-content:center}
.hero__more{position:absolute;left:0;width:1200px;top:584px;text-align:center;color:var(--white);font-family:'Montserrat',sans-serif;font-weight:600;font-size:11px;letter-spacing:1.5px}

/* Intro */
.intro__blob{position:absolute;left:0;top:650px;width:600px;height:570px}
.intro__photo{position:absolute;left:139px;top:731px;width:434px;height:372px}
.intro__text{position:absolute;left:649px;top:796px;width:410px}
.h2{font-weight:700;font-size:28px;line-height:36px;color:var(--ink)}
.h2 .blue{color:var(--blue-700)}.green{color:var(--green-600)}
.body{font-size:13px;line-height:24.3px;color:#222}
.intro__text .body{margin-top:14px;text-align:justify}

/* Products */
.products__head{position:absolute;left:0;top:1278px;width:1200px;text-align:center}
.products__head .h2{color:var(--blue-700)}
.products__head .body{margin-top:8px;line-height:20px}
.product__blob{position:absolute;left:640px;top:1336px;width:560px;height:520px}
.product__graphic{position:absolute;left:649px;top:1455px;width:410px;height:340px}
.product__text{position:absolute;left:142px;top:1456px;width:415px}
.h3{font-weight:500;font-size:19px;line-height:27px;color:var(--ink)}
.product__text .body{margin-top:12px;line-height:23px}
.btn-outline{position:absolute;height:38px;border:1.5px solid var(--green-600);border-radius:20px;background:var(--white);display:flex;align-items:center;justify-content:center;font-size:13px;font-weight:500;color:#222}

.quality__bg{position:absolute;left:0;top:1858px;width:1200px;height:680px}
.quality__graphic{position:absolute;left:150px;top:1945px;width:420px;height:385px}
.quality__text{position:absolute;left:651px;top:2005px;width:415px}
.quality__text .body{margin-top:14px;line-height:23px}

/* CTA */
.cta__photo{position:absolute;left:649px;top:2533px;width:551px;height:353px;
  background:
   radial-gradient(ellipse 120px 150px at 38% 55%,rgba(178,122,84,.55),transparent 75%),
   radial-gradient(ellipse 130px 160px at 64% 45%,rgba(214,178,120,.55),transparent 75%),
   linear-gradient(90deg,#ffffff 0%,rgba(255,255,255,0) 22%),
   linear-gradient(180deg,#eef2f6 0%,#9fb4cc 65%,#5c7796 100%)}
.cta__title{position:absolute;left:142px;top:2660px;width:480px;font-weight:700;font-size:24.5px;line-height:32px;color:var(--blue-700)}

/* Footer */
.footer{position:absolute;left:0;top:2886px;width:1200px;height:310px;background:var(--blue-900);color:var(--white);font-family:'Poppins',sans-serif;overflow:hidden}
.footer__glow{position:absolute;inset:0;background:radial-gradient(ellipse 160px 200px at 0% 40%,rgba(6,119,186,.35),transparent 75%),radial-gradient(ellipse 200px 140px at 100% 0%,rgba(6,119,186,.35),transparent 75%)}
.footer .logo{position:absolute;left:137px;top:92px;color:var(--white)}
.footer__tag{position:absolute;left:140px;top:146px;font-size:12.5px;line-height:23px}
.social{position:absolute;left:140px;top:214px;display:flex;gap:22px}
.social span{width:24px;height:24px;border-radius:50%;background:rgba(255,255,255,.18)}
.fcol{position:absolute;top:98px}
.fcol h4{font-size:15px;font-weight:600;position:relative;padding-bottom:14px}
.fcol h4::after{content:"";position:absolute;left:0;bottom:0;width:24px;height:2px;background:var(--green-500)}
.fcol ul{list-style:none;margin-top:16px;font-size:12.5px}
.fcol li{height:28px}
.fcol li::before{content:"▸";color:var(--green-500);font-size:10px;margin-right:10px}
.contact{display:flex;align-items:center;gap:14px;font-size:13px;margin-top:14px}
.contact i{width:32px;height:32px;border-radius:50%;background:rgba(255,255,255,.15);display:flex;align-items:center;justify-content:center}
.news__input{margin-top:20px;width:197px;height:39px;border:1px solid rgba(255,255,255,.5);border-radius:20px;font-size:11px;color:#c8d2e6;display:flex;align-items:center;padding-left:22px}
.news__btn{margin-top:20px;width:197px;height:37px;border-radius:20px;background:var(--blue-500);font-size:13px;font-weight:600;display:flex;align-items:center;justify-content:center}
.bottombar{position:absolute;left:0;top:3196px;width:1200px;height:50px;background:var(--blue-800);color:var(--white);font-family:'Poppins',sans-serif;font-size:12px;display:flex;align-items:center;justify-content:space-between;padding:0 142px 0 140px}
</style>
</head>
<body>

<header class="hero">
  <div class="hero__band"></div>
  <div class="hero__photo" role="img" aria-label="Foto: Datenstrom aus Binärcode, der in ein leuchtendes Netzwerk-Symbol mündet"></div>
  <nav class="nav">
    <div class="logo"><span class="logo__dot"></span>QR.KA Horizon</div>
    <div class="nav__menu">
      <span class="is-active">Heim</span>
      <span>Lösungen<span class="caret">▼</span></span>
      <span>Wer Sind Wir<span class="caret">▼</span></span>
    </div>
    <div class="nav__cta">Kontaktieren Sie Uns</div>
  </nav>
  <h1 class="hero__title">Mit Präzision<br>Die Zukunft<br>Vorantreiben</h1>
  <p class="hero__sub">Innovative Lösungen für Leistung,<br>Sicherheit und Skalierbarkeit</p>
  <div class="hero__btn">Legen Sie Los</div>
  <div class="hero__more">ENTDECKEN SIE MEHR
    <svg width="16" height="10" viewBox="0 0 16 10" style="display:block;margin:10px auto 0"><path d="M2 2l6 6 6-6" fill="none" stroke="#fff" stroke-width="2"/></svg>
  </div>
</header>

<section class="intro">
  <svg class="intro__blob" viewBox="0 0 600 570" aria-hidden="true"><path d="M0 110 C60 40 200 0 300 2 C340 4 330 120 420 200 C500 270 640 240 590 380 C540 520 360 570 240 568 C130 566 40 520 0 470 Z" fill="#E8F1F8"/></svg>
  <svg class="intro__photo" viewBox="0 0 434 372" role="img" aria-label="Foto: zwei Kolleginnen und Kollegen arbeiten gemeinsam am Bildschirm">
    <defs><linearGradient id="ip" x1="0" y1="0" x2="1" y2="1"><stop offset="0" stop-color="#8d8f92"/><stop offset=".45" stop-color="#c7c2bb"/><stop offset=".75" stop-color="#6d7884"/><stop offset="1" stop-color="#3a4654"/></linearGradient></defs>
    <path d="M40 70 C90 20 200 0 300 10 C400 22 440 90 430 170 C420 250 360 350 250 368 C140 384 40 330 10 250 C-10 190 0 110 40 70 Z" fill="url(#ip)"/>
  </svg>
  <div class="intro__text">
    <h2 class="h2"><span class="blue">QR.KA</span> <span class="green">Horizon</span>-Ihr Partner für ganzheitliche Softwarelösungen</h2>
    <p class="body">QR.KA Horizon ist ein dynamisches Unternehmen, das sich nicht nur auf die Konzeption, Gestaltung und Entwicklung von Individualsoftware spezialisiert hat, sondern auch für deren reibungslosen Betrieb sorgt. Mit einem Team aus erfahrenen Softwarearchitekten und IT-Profis verbinden wir modernste Softwareentwicklung mit fundiertem IT-Know-how - für Lösungen, die nachhaltig, leistungsstark und zukunftssicher sind.</p>
  </div>
</section>

<section class="products">
  <div class="products__head">
    <h2 class="h2"><span>Ausgewähltes</span> <span class="green">Produkt</span></h2>
    <p class="body">Lorem ipsum dolor sit amet, consectetuer adipiscing elit, sed diam nonummy nibh euismod<br>tincidunt ut laoreet dolore magna aliquam erat volutpat wisi enim ad minim veniam</p>
  </div>

  <svg class="product__blob" viewBox="0 0 560 520" aria-hidden="true"><defs><linearGradient id="pb" x1="0" y1="0" x2="1" y2="1"><stop offset="0" stop-color="#0b3fa8"/><stop offset="1" stop-color="#0a2a7c"/></linearGradient></defs><path d="M560 0 C520 120 420 150 260 140 C110 130 40 220 80 330 C110 420 60 470 0 470 C120 500 280 520 560 510 Z" fill="url(#pb)"/></svg>
  <svg class="product__graphic" viewBox="0 0 410 340" role="img" aria-label="Architekturgrafik: zwei Laptops tauschen über eine zentrale Schnittstelle Daten aus">
    <defs><linearGradient id="pg" x1="0" y1="0" x2="1" y2="1"><stop offset="0" stop-color="#8a78e6"/><stop offset=".55" stop-color="#5a46c4"/><stop offset="1" stop-color="#4fe3d0"/></linearGradient></defs>
    <path d="M20 60 L150 10 L205 80 L265 20 L395 60 L395 250 L205 335 L15 250 Z" fill="url(#pg)" opacity=".92"/>
  </svg>
  <div class="product__text">
    <h3 class="h3">Offene Datenaustauschschnittstelle <span class="green">(CLURA)</span></h3>
    <p class="body">Sie verwenden eine relationale Datenbank (Brightcask, Tabulon Hub, Vellumdb usw.) und möchten ausgewählte Daten mit Dritten teilen - sei es für ein Data Warehouse, Business Controller, Lieferanten oder Kunden? Sie wollen aber die Datensicherheit, -integrität und -verfügbarkeit Ihrer primären Lösung in keiner Weise gefährden? Mit unserer Lösung erhalten Sie genau das: maximalen Schutz für Ihre Anwendung bei gleichzeitiger Nutzung durch autorisierte Dritte - ohne die teuren Lizenzkosten für eine Schattendatenbank.<br>Lassen Sie uns gemeinsam herausfinden, wie Sie Ihre Daten sicher und effizient nutzen können.</p>
  </div>
  <div class="btn-outline" style="left:141px;top:1749px;width:155px">Kontaktieren Sie uns</div>

  <svg class="quality__bg" viewBox="0 0 1200 680" aria-hidden="true"><defs><linearGradient id="qb" x1="0" y1="0" x2="1" y2="1"><stop offset="0" stop-color="#0b2f8c"/><stop offset="1" stop-color="#0a2060"/></linearGradient></defs><path d="M0 0 C400 40 800 -10 1200 20 L1200 520 C900 700 300 700 0 560 Z" fill="#F1F6FB"/><path d="M0 0 L380 40 C460 60 470 160 560 220 C620 260 600 400 560 440 C460 400 300 460 120 450 C60 448 20 470 0 500 Z" fill="url(#qb)"/></svg>
  <svg class="quality__graphic" viewBox="0 0 420 385" role="img" aria-label="Illustration: Laptop mit Lupe, die Farbabweichungen im Code prüft">
    <defs><linearGradient id="qg" x1="0" y1="0" x2="1" y2="1"><stop offset="0" stop-color="#2a4fc4"/><stop offset=".55" stop-color="#6b4fd8"/><stop offset="1" stop-color="#c4a8f4"/></linearGradient></defs>
    <path d="M100 40 L260 0 L320 40 L300 160 L400 220 L220 380 L20 280 L40 200 L110 160 Z" fill="url(#qg)"/>
  </svg>
  <div class="quality__text">
    <h3 class="h3">Software zur Qualitätssicherung der Farbgenauigkeit <span class="green">( MIVO)</span></h3>
    <p class="body">MIVO ist die intelligente Lösung für Unternehmen, die bei der Farbgenauigkeit keine Kompromisse eingehen. Die Software erkennt automatisch Farbabweichungen zwischen Mustern, beschreibt sie eindeutig und sorgt so für eine gleichbleibend hohe Produktqualität - schnell, visuell und präzise. Perfekt für alle, die Farbe zur Vertrauenssache machen.</p>
  </div>
  <div class="btn-outline" style="left:650px;top:2234px;width:154px">Kontaktieren Sie uns</div>
</section>

<section class="cta">
  <div class="cta__photo" role="img" aria-label="Foto: zwei Personen blicken gemeinsam auf einen Laptop"></div>
  <h2 class="cta__title">Ermutigung der Besucher, sich mit Ihnen<br>in Verbindung zu setzen, um Lösungen<br><span class="green">für die sichere und effiziente Nutzung<br>ihrer Daten zu finden.</span></h2>
  <div class="btn-outline" style="left:141px;top:2807px;width:155px">Kontaktieren Sie uns</div>
</section>

<footer class="footer">
  <div class="footer__glow"></div>
  <div class="logo"><span class="logo__dot"></span>QR.KA Horizon</div>
  <p class="footer__tag">Innovative Software trifft auf<br>echte IT-Expertise</p>
  <div class="social" aria-label="Soziale Medien"><span></span><span></span><span></span><span></span></div>
  <div class="fcol" style="left:435px">
    <h4>Quicklinks</h4>
    <ul><li>Heim</li><li>Lösungen</li><li>Wer Sind Wir</li><li>Kontakt</li></ul>
  </div>
  <div class="fcol" style="left:616px">
    <h4>Kontakt Uns</h4>
    <div class="contact"><i><svg width="14" height="14" viewBox="0 0 24 24"><path d="M6.6 10.8a15 15 0 006.6 6.6l2.2-2.2c.3-.3.7-.4 1-.2 1.1.4 2.3.6 3.6.6.6 0 1 .4 1 1V20c0 .6-.4 1-1 1A17 17 0 013 4c0-.6.4-1 1-1h3.5c.6 0 1 .4 1 1 0 1.3.2 2.5.6 3.6.1.3 0 .7-.2 1z" fill="#fff"/></svg></i>(040)-318-2297</div>
    <div class="contact"><i><svg width="14" height="12" viewBox="0 0 24 18"><rect x="1" y="1" width="22" height="16" rx="2" fill="none" stroke="#fff" stroke-width="2"/><path d="M2 2l10 8 10-8" fill="none" stroke="#fff" stroke-width="2"/></svg></i>info@qrka-horizon.de</div>
  </div>
  <div class="fcol" style="left:861px;top:96px">
    <h4>Newsletter Abonnieren</h4>
    <div class="news__input">Eingeben E-Mail</div>
    <div class="news__btn">Jetzt Abonnieren</div>
  </div>
</footer>
<div class="bottombar"><span>Copyright © 2025 QrKa Horizon Software Engineering Technology | Alle Rechte Vorbehalten.</span><span>Impressum</span></div>

</body>
</html>
```